We need a business card design, letterhead design and envelope design for our corporate image

We are looking for a corporate business card design, letterhead and envelope design to match the business card design. Logo is done.

```html
<!DOCTYPE html>
<html lang="en">
<head>
<meta charset="UTF-8">
<title>Norvane Business Card</title>
<link href="https://fonts.googleapis.com/css2?family=Montserrat:wght@400;500;700&display=swap" rel="stylesheet">
<style>
  :root {
    --backdrop: #2a2a2e;
    --card: #1f1f20;
    --accent: #f5c400;
    --ink-light: #ffffff;
    --ink-muted: #e6e6e6;
    --emboss: #5a5a5c;
  }
  html, body {
    margin: 0;
    padding: 0;
    width: 1200px;
    height: 786px;
    overflow: hidden;
    background: var(--backdrop);
    font-family: "Montserrat", sans-serif;
  }
  .canvas {
    position: relative;
    width: 1200px;
    height: 786px;
    display: flex;
    align-items: center;
    justify-content: center;
    gap: 40px;
  }
  .card {
    position: relative;
    width: 520px;
    height: 298px;
    background: var(--card);
    border: 6px solid var(--accent);
    box-sizing: border-box;
    box-shadow: 0 14px 30px rgba(0,0,0,0.45);
  }
  .card-front {
    display: flex;
    align-items: center;
  }
  .brand {
    display: flex;
    align-items: center;
    gap: 12px;
    padding-left: 46px;
    width: 230px;
    box-sizing: border-box;
  }
  .brand-square {
    width: 26px;
    height: 26px;
    border: 4px solid var(--accent);
    box-sizing: border-box;
    flex: none;
  }
  .brand-name {
    font-weight: 700;
    font-size: 34px;
    color: var(--ink-light);
    letter-spacing: -0.5px;
  }
  .divider {
    width: 1.5px;
    height: 118px;
    background: var(--accent);
    margin: 0 24px 0 6px;
  }
  .contact {
    color: var(--ink-muted);
  }
  .contact-name {
    margin: 0;
    font-size: 19px;
    font-weight: 500;
    color: var(--accent);
    letter-spacing: 0.8px;
    text-transform: uppercase;
  }
  .contact-role {
    margin: 2px 0 14px;
    font-size: 13px;
  }
  .contact-list {
    list-style: none;
    margin: 0;
    padding: 0;
    font-size: 12.5px;
    line-height: 20px;
  }
  .contact-list li {
    display: flex;
    align-items: center;
    gap: 8px;
  }
  .contact-list svg {
    width: 10px;
    height: 10px;
    flex: none;
  }
  .card-back {
    display: flex;
    align-items: center;
    justify-content: center;
  }
  .brand-emboss {
    display: flex;
    align-items: center;
    gap: 16px;
  }
  .brand-emboss .brand-square {
    width: 34px;
    height: 34px;
    border: 5px solid var(--emboss);
  }
  .brand-emboss .brand-name {
    font-size: 48px;
    color: var(--emboss);
  }
</style>
</head>
<body>
<main class="canvas">
  <section class="card card-front" aria-label="Business card front">
    <div class="brand">
      <span class="brand-square"></span>
      <span class="brand-name">Norvane</span>
    </div>
    <div class="divider"></div>
    <div class="contact">
      <h1 class="contact-name">Daniel Brooks</h1>
      <p class="contact-role">Director</p>
      <ul class="contact-list">
        <li>
          <svg viewBox="0 0 10 10"><path d="M2 1 L4 1 L4.6 3 L3.4 3.8 Q4.4 5.8 6.2 6.6 L7 5.4 L9 6 L9 8 Q5 9 1.5 5 Q1 3 2 1 Z" fill="var(--accent)"/></svg>
          <span>+1 555 014-3870</span>
        </li>
        <li>
          <svg viewBox="0 0 10 10"><rect x="0.8" y="2" width="8.4" height="6" fill="none" stroke="var(--accent)" stroke-width="1"/><path d="M0.8 2 L5 5.4 L9.2 2" fill="none" stroke="var(--accent)" stroke-width="1"/></svg>
          <span>hello@norvane.com</span>
        </li>
        <li>
          <svg viewBox="0 0 10 10"><circle cx="5" cy="5" r="4" fill="none" stroke="var(--accent)" stroke-width="1"/><ellipse cx="5" cy="5" rx="1.8" ry="4" fill="none" stroke="var(--accent)" stroke-width="0.8"/><line x1="1" y1="5" x2="9" y2="5" stroke="var(--accent)" stroke-width="0.8"/></svg>
          <span>www.norvane.com</span>
        </li>
        <li>
          <svg viewBox="0 0 10 10"><path d="M5 9.5 Q1.5 5.5 1.5 3.6 A3.5 3.5 0 0 1 8.5 3.6 Q8.5 5.5 5 9.5 Z" fill="var(--accent)"/><circle cx="5" cy="3.6" r="1.3" fill="var(--card)"/></svg>
          <span>Dover, DE USA</span>
        </li>
      </ul>
    </div>
  </section>

  <section class="card card-back" aria-label="Business card back">
    <div class="brand-emboss">
      <span class="brand-square"></span>
      <span class="brand-name">Norvane</span>
    </div>
  </section>
</main>
</body>
</html>
```